New Business Card Design for Manufacturing

We are an engineering/manufacturing company that offers Advanced machining/assembly/engineering services, as well as innovative products for the heavy duty engine cooling markets.

We are looking to get a new business card designed that is clean and modern looking, but still fits the wide range of technical/skilled work we do.

- We hope to use this design as the base for other design work in new Presentations, web, and print work.

Industry/Entity Type

Engineering

Contact Information for Business Card

Our preferred color of blue is (RGB) 22/71/159 but can vary slightly from that color. Our content will be our Logo and full company name (Vantrell Forge Works, Inc.), company address, name, job title, phone number with extension, cell number, fax number, website, and email address on the cards.
We'd like the full company name next to the logo, but we are open to other interpretations of that layout.
Preferably, we would like the back side to be clean with just our logo, and the front to contain all of the contact information.

Colors
2f74b4
0355a3
85abd2

Requirements
Must have
• - Logo, company name, needed content - We are open to interpretation beyond that.
• - Standard size business card.
• - Horizontal orientation.
• - Enough space for lengthy names / job titles (for example, a job title could read "Directory of Human Resources" or "V.P. of Governmental Affairs"). We need this to look clean, whether the title be short (CEO) or long (as described above).

```html
<!DOCTYPE html>
<html lang="en">
<head>
<meta charset="utf-8">
<title>Vantrell Forge Works – Business Card</title>
<link rel="stylesheet" href="https://fonts.googleapis.com/css2?family=Open+Sans:wght@400;600;700;800&display=swap">
<style>
  :root {
    --page-bg: #8d8d8d;
    --card-white: #ffffff;
    --brand-blue: #0c55a3;
    --brand-deep: #16479f;
    --sky-blue: #4db3e6;
    --tab-mid: #a5cdee;
    --tab-light: #d3e6f7;
    --frame-lilac: #8d9ddb;
    --text-dark: #3d3d3d;
    --text-grey: #8a8a8a;
    --wordmark-blue: #2f9be0;
  }
  * { margin: 0; padding: 0; box-sizing: border-box; }
  html, body { width: 1200px; height: 1000px; overflow: hidden; }
  body {
    background: var(--page-bg);
    font-family: "Open Sans", Arial, sans-serif;
    position: relative;
  }
  .card {
    position: absolute;
    left: 250px;
    width: 700px;
    height: 400px;
    overflow: hidden;
    box-shadow: 0 10px 30px rgba(0,0,0,.35);
  }
  .card--front { top: 90px; background: var(--card-white); }
  .card--back { top: 530px; background: var(--brand-blue); }

  /* front */
  .company-name {
    position: absolute; left: 34px; top: 40px;
    color: var(--wordmark-blue);
    font-weight: 800; font-size: 20px; line-height: 21px;
    text-transform: uppercase; letter-spacing: .3px;
  }
  .brand-mark {
    position: absolute; right: 34px; top: 30px;
    display: flex; flex-direction: column; align-items: flex-end;
  }
  .brand-mark__name {
    display: flex; align-items: center; gap: 8px;
    color: var(--brand-deep); font-weight: 800; font-size: 28px; line-height: 30px;
  }
  .brand-mark__square { width: 14px; height: 14px; background: var(--brand-deep); }
  .brand-mark__tagline {
    color: var(--brand-deep); font-weight: 700; font-size: 10px; letter-spacing: .5px;
    text-transform: uppercase; margin-top: 2px;
  }
  .person {
    position: absolute; left: 240px; top: 100px;
    color: var(--text-dark); text-transform: uppercase;
  }
  .person__name { font-size: 24px; font-weight: 400; letter-spacing: 1px; }
  .person__title { font-size: 13px; letter-spacing: 1px; margin-top: 2px; }
  .ribbon { position: absolute; left: 0; top: 0; width: 700px; height: 400px; }
  .address {
    position: absolute; left: 310px; top: 188px;
    color: #fff; font-size: 14px; letter-spacing: 1px; text-transform: uppercase;
    display: flex; align-items: center; gap: 12px;
  }
  .contact-list {
    position: absolute; list-style: none;
    color: var(--text-grey); font-size: 14px; letter-spacing: 1px; text-transform: uppercase;
  }
  .contact-list li { display: flex; align-items: center; gap: 12px; height: 26px; }
  .contact-list svg { width: 14px; height: 14px; fill: var(--text-grey); }
  .contact-list--phones { left: 40px; top: 292px; }
  .contact-list--web { left: 400px; top: 232px; }

  /* back */
  .back-frame { position: absolute; inset: 0; }
  .back-brand {
    position: absolute; left: 0; right: 0; top: 128px;
    text-align: center; color: #fff;
  }
  .back-brand__name { font-weight: 800; font-size: 72px; line-height: 80px; letter-spacing: 2px; }
  .back-brand__tagline { font-weight: 700; font-size: 21px; text-transform: uppercase; letter-spacing: .5px; }
  .back-website {
    position: absolute; left: 0; right: 0; top: 322px;
    text-align: center; color: #fff; font-size: 18px;
  }
</style>
</head>
<body>

<section class="card card--front" aria-label="Business card front">
  <svg class="ribbon" viewBox="0 0 700 400" aria-hidden="true">
    <path d="M40 240 Q40 208 80 208 L160 208 L160 240 Z" fill="var(--tab-light)"/>
    <path d="M120 240 Q120 200 170 200 L250 200 L250 240 Z" fill="var(--tab-mid)"/>
    <path d="M220 240 Q220 200 270 196 L700 160 L700 190 L270 240 Z" fill="var(--sky-blue)"/>
    <rect x="220" y="168" width="480" height="26" fill="var(--sky-blue)"/>
  </svg>

  <h1 class="company-name">Vantrell<br>Forge<br>Works <span style="font-size:10px">Inc</span></h1>

  <div class="brand-mark">
    <div class="brand-mark__name"><span class="brand-mark__square"></span>Vantrell</div>
    <div class="brand-mark__tagline">Shaping What Drives</div>
  </div>

  <div class="person">
    <p class="person__name">Name of CEO</p>
    <p class="person__title">Directory of Human Resources</p>
  </div>

  <p class="address">
    <svg width="12" height="16" viewBox="0 0 12 16" aria-hidden="true"><path d="M6 0a6 6 0 0 0-6 6c0 4.5 6 10 6 10s6-5.5 6-10a6 6 0 0 0-6-6zm0 8.5A2.5 2.5 0 1 1 6 3.5a2.5 2.5 0 0 1 0 5z" fill="#fff"/></svg>
    Your Company Address
  </p>

  <ul class="contact-list contact-list--web">
    <li><svg viewBox="0 0 16 16" aria-hidden="true"><circle cx="8" cy="8" r="7"/></svg>Website</li>
    <li><svg viewBox="0 0 16 16" aria-hidden="true"><path d="M1 3h14v10H1z"/></svg>Email Address</li>
  </ul>

  <ul class="contact-list contact-list--phones">
    <li><svg viewBox="0 0 16 16" aria-hidden="true"><path d="M2 5q6-5 12 0v2h-3V5.5Q8 4.5 5 5.5V7H2z M4 9h8l2 5H2z"/></svg>Phone Number</li>
    <li><svg viewBox="0 0 16 16" aria-hidden="true"><path d="M3 1l3 1 1 3-2 2q1 3 4 4l2-2 3 1 1 3-2 2Q3 13 1 3z"/></svg>Cell Number</li>
    <li><svg viewBox="0 0 16 16" aria-hidden="true"><path d="M4 1h8v4H4z M1 6h14v7h-3v2H4v-2H1z"/></svg>Fax Number</li>
  </ul>
</section>

<section class="card card--back" aria-label="Business card back">
  <svg class="back-frame" viewBox="0 0 700 400" aria-hidden="true">
    <polyline points="230,360 60,360 60,40 640,40 640,360 470,360" fill="none" stroke="var(--frame-lilac)" stroke-width="3"/>
  </svg>
  <div class="back-brand">
    <p class="back-brand__name">VANTRELL</p>
    <p class="back-brand__tagline">Shaping What Drives</p>
  </div>
  <p class="back-website">www.website.com</p>
</section>

</body>
</html>
```